Nivel Crest - Powerpoint Templates

We are a consultancy to help builders to optimize their planning in order to save building costs. For that reason we need templates for teasers and presentations where we offer our services, show our team and their capacities and present workflows, organization charts, price lists etc.

```html
<!DOCTYPE html>
<html lang="en">
<head>
<meta charset="utf-8">
<title>Nivel Crest – Presentation Template</title>
<link href="https://fonts.googleapis.com/css2?family=Montserrat:wght@400;500;600;700;800&display=swap" rel="stylesheet">
<style>
:root{
  --page:#d6d6d6;
  --gold:#c8963a;
  --gold-light:#e5c06a;
  --gold-dark:#9c7226;
  --ink:#2b2b30;
  --grey:#6f6f74;
  --white:#ffffff;
}
*{margin:0;padding:0;box-sizing:border-box}
html,body{width:772px;height:1200px;overflow:hidden;background:var(--page)}
body{position:relative;font-family:"Montserrat",Arial,sans-serif;color:var(--ink)}
.slide{position:absolute;width:287px;height:180px;background:var(--white);overflow:hidden;box-shadow:0 4px 6px rgba(0,0,0,.18)}
.abs{position:absolute}
.photo-gold{background:linear-gradient(125deg,#b8862f 0%,#d4a84c 45%,#c49338 75%,#8f6a2a 100%)}
.photo-office{background:linear-gradient(100deg,#8a8c90 0%,#c9c6c0 40%,#a9a39a 70%,#d8d4ce 100%)}
.brand{font-weight:700;color:var(--gold);letter-spacing:.3px;white-space:nowrap}
.brand-lg{font-size:10px}
.brand-sm{font-size:4.5px}
.footer-line{position:absolute;left:0;top:162px;width:100%;height:1.5px;background:var(--ink)}
.footer-brand{position:absolute;left:10px;top:168px}
.footer-page{position:absolute;right:10px;top:169px;font-size:3.5px;color:var(--gold);font-weight:600}
.footer-page b{color:var(--ink)}
.lorem{font-size:3.6px;line-height:1.35}
.center{text-align:center}
.heading-gold{color:var(--gold);font-weight:600}
.icon{position:absolute;width:12px;height:12px;border-radius:50%;background:var(--gold);border:1px solid var(--white)}
.icon svg{width:100%;height:100%;display:block}
</style>
</head>
<body>

<!-- Title slide -->
<section class="slide" style="left:78px;top:78px">
  <div class="abs" style="left:12px;top:14px;display:flex;align-items:center;gap:4px">
    <span style="width:10px;height:10px;background:var(--gold);display:block"></span>
    <span class="brand brand-lg">NIVEL CREST</span>
  </div>
  <div class="abs" role="img" aria-label="Office tower photograph with gold overlay" style="left:0;top:41px;width:287px;height:115px;background:linear-gradient(90deg,#c0903a 0%,#d0a552 40%,#b8b8a8 62%,#9fb2c6 80%,#cfdceb 100%)"></div>
  <h1 class="abs" style="left:12px;top:87px;font-size:12px;line-height:13px;font-weight:700;color:var(--white)">PRESENTATION<br>TITLE GOES HERE</h1>
  <p class="abs" style="left:12px;top:117px;font-size:4.6px;color:var(--white)">Subtitle of Presentation Goes Here</p>
  <p class="abs" style="left:12px;top:140px;font-size:4.2px;color:var(--white)">Friday, July 08, 2023</p>
  <p class="abs center" style="left:0;width:287px;top:164px;font-size:4.4px;color:var(--grey)">© Copyright Nivel Crest All Right Reserved</p>
</section>

<!-- Services list slide -->
<section class="slide" style="left:405px;top:78px">
  <div class="abs photo-gold" role="img" aria-label="Office tower photograph in gold tones" style="left:0;top:37px;width:163px;height:105px;clip-path:polygon(0 0,120px 0,163px 100%,0 100%)"></div>
  <div class="icon" style="left:120px;top:47px"><svg viewBox="0 0 12 12"><circle cx="6" cy="4.5" r="1.7" fill="#fff"/><path d="M3 9.3c.4-2 1.6-2.8 3-2.8s2.6.8 3 2.8z" fill="#fff"/></svg></div>
  <div class="icon" style="left:129px;top:71px"><svg viewBox="0 0 12 12"><circle cx="6" cy="4.5" r="1.7" fill="#fff"/><path d="M3 9.3c.4-2 1.6-2.8 3-2.8s2.6.8 3 2.8z" fill="#fff"/></svg></div>
  <div class="icon" style="left:139px;top:94px"><svg viewBox="0 0 12 12"><circle cx="6" cy="4.5" r="1.7" fill="#fff"/><path d="M3 9.3c.4-2 1.6-2.8 3-2.8s2.6.8 3 2.8z" fill="#fff"/></svg></div>
  <div class="icon" style="left:148px;top:118px"><svg viewBox="0 0 12 12"><circle cx="6" cy="4.5" r="1.7" fill="#fff"/><path d="M3 9.3c.4-2 1.6-2.8 3-2.8s2.6.8 3 2.8z" fill="#fff"/></svg></div>
  <div class="abs" style="left:142px;top:47px"><p style="font-size:6.4px">Service Title Goes Here</p><p style="font-size:3.4px">Vivomus eu dull ex. curobour dopibus</p></div>
  <div class="abs" style="left:152px;top:71px"><p style="font-size:6.4px">Service Title Goes Here</p><p style="font-size:3.4px">Vivomus eu dull ex. curobour dopibus</p></div>
  <div class="abs" style="left:161px;top:94px"><p style="font-size:6.4px">Service Title Goes Here</p><p style="font-size:3.4px">Vivomus eu dull ex. curobour dopibus</p></div>
  <div class="abs" style="left:171px;top:117px"><p style="font-size:6.4px">Service Title Goes Here</p><p style="font-size:3.4px">Vivomus eu dull ex. curobour dopibus</p></div>
  <div class="footer-line"></div>
  <span class="footer-brand brand brand-sm">NIVEL CREST</span>
  <span class="footer-page">NIVEL CREST <b>| 01</b></span>
</section>

<!-- Our Service – icon row -->
<section class="slide" style="left:78px;top:290px">
  <div class="abs photo-gold" role="img" aria-label="Office tower photograph in gold tones" style="left:0;top:0;width:287px;height:91px"></div>
  <h2 class="abs center" style="left:0;width:287px;top:8px;font-size:9.5px;font-weight:400;color:var(--white)">Our <b>Service</b></h2>
  <div class="abs" style="left:114px;top:21px;width:60px;height:.6px;background:var(--white)"></div>
  <p class="abs lorem center" style="left:50px;width:187px;top:28px;color:var(--white)">Lorem ipsum dolor sit amet, consectetuer adipiscing elit, sed diam nonummy nibh euismod tincidunt ut laoreet dolore magna aliquam erat volutpat. Ut wisi enim ad minim veniam, quis nostrud exerci tation ullamcorper suscipit lobortis nisl ut aliquip ex ea commodo consequat. Duis autem vel eum iriure dolor in hendrerit in vulputate velit esse molestie consequat.</p>
  <svg class="abs" style="left:0;top:60px" width="287" height="40" viewBox="0 0 287 40">
    <g fill="none" stroke="#fff" stroke-width="1">
      <circle cx="37.5" cy="14" r="10.5"/><circle cx="90.5" cy="14" r="10.5"/><circle cx="143" cy="14" r="10.5"/><circle cx="196.5" cy="14" r="10.5"/><circle cx="249.5" cy="14" r="10.5"/>
    </g>
    <g fill="#fff">
      <circle cx="37.5" cy="11" r="2.2"/><path d="M33.5 18c.5-2.7 2-3.7 4-3.7s3.5 1 4 3.7z"/>
      <circle cx="90.5" cy="11" r="2.2"/><path d="M86.5 18c.5-2.7 2-3.7 4-3.7s3.5 1 4 3.7z"/>
      <circle cx="143" cy="11" r="2.2"/><path d="M139 18c.5-2.7 2-3.7 4-3.7s3.5 1 4 3.7z"/>
      <circle cx="196.5" cy="11" r="2.2"/><path d="M192.5 18c.5-2.7 2-3.7 4-3.7s3.5 1 4 3.7z"/>
      <circle cx="249.5" cy="11" r="2.2"/><path d="M245.5 18c.5-2.7 2-3.7 4-3.7s3.5 1 4 3.7z"/>
    </g>
    <g stroke="var(--gold)" stroke-width=".6"><line x1="37.5" y1="24.5" x2="37.5" y2="32"/><line x1="90.5" y1="24.5" x2="90.5" y2="32"/><line x1="143" y1="24.5" x2="143" y2="32"/><line x1="196.5" y1="24.5" x2="196.5" y2="32"/><line x1="249.5" y1="24.5" x2="249.5" y2="32"/></g>
  </svg>
  <div class="abs center" style="left:12.5px;width:50px;top:96px"><p style="font-size:6px;line-height:6.5px">Service Title<br>Goes Here</p><p style="font-size:3.4px;margin-top:6px">Vivomus eu dull ex.<br>curobour dopibus</p></div>
  <div class="abs center" style="left:65.5px;width:50px;top:96px"><p style="font-size:6px;line-height:6.5px">Service Title<br>Goes Here</p><p style="font-size:3.4px;margin-top:6px">Vivomus eu dull ex.<br>curobour dopibus</p></div>
  <div class="abs center" style="left:118px;width:50px;top:96px"><p style="font-size:6px;line-height:6.5px">Service Title<br>Goes Here</p><p style="font-size:3.4px;margin-top:6px">Vivomus eu dull ex.<br>curobour dopibus</p></div>
  <div class="abs center" style="left:171.5px;width:50px;top:96px"><p style="font-size:6px;line-height:6.5px">Service Title<br>Goes Here</p><p style="font-size:3.4px;margin-top:6px">Vivomus eu dull ex.<br>curobour dopibus</p></div>
  <div class="abs center" style="left:224.5px;width:50px;top:96px"><p style="font-size:6px;line-height:6.5px">Service Title<br>Goes Here</p><p style="font-size:3.4px;margin-top:6px">Vivomus eu dull ex.<br>curobour dopibus</p></div>
  <div class="footer-line"></div>
  <span class="footer-brand brand brand-sm">NIVEL CREST</span>
  <span class="footer-page">NIVEL CREST <b>| 01</b></span>
</section>

<!-- About Us -->
<section class="slide" style="left:405px;top:290px">
  <div class="abs photo-gold" role="img" aria-label="Office tower photograph in gold tones" style="left:205px;top:0;width:82px;height:140px"></div>
  <div class="abs" style="left:142px;top:11px;width:124px;height:119px;background:var(--white)"></div>
  <div class="abs photo-office" role="img" aria-label="Team working at laptops in a bright office" style="left:144px;top:13px;width:117px;height:114px"></div>
  <h2 class="abs center" style="left:15px;width:100px;top:29px;font-size:9.5px;font-weight:400;color:var(--gold)">About <b>Us</b></h2>
  <div class="abs" style="left:35px;top:42px;width:60px;height:.6px;background:var(--gold)"></div>
  <p class="abs lorem center" style="left:12px;width:112px;top:56px;font-size:4px">Lorem ipsum dolor sit amet, consectetuer adipiscing elit, sed diam nonummy nibh euismod tincidunt ut laoreet dolore magna aliquam erat volutpat. Ut wisi enim ad minim veniam, quis nostrud exerci tation ullamcorper suscipit lobortis<br>Lorem ipsum dolor sit amet, consectetuer adipiscing elit, sed diam nonummy nibh euismod tincidunt ut laoreet dolore magna aliquam erat volutpat. Ut wisi enim ad minim veniam, quis nostrud exerci tation ullamcorper suscipit lobortis</p>
  <div class="footer-line"></div>
  <span class="footer-brand brand brand-sm">NIVEL CREST</span>
  <span class="footer-page">NIVEL CREST <b>| 01</b></span>
</section>

<!-- Heading with three columns -->
<section class="slide" style="left:78px;top:502px">
  <div class="abs photo-gold" role="img" aria-label="Office tower photograph in gold tones" style="left:93px;top:0;width:194px;height:143px"></div>
  <div class="abs photo-office" role="img" aria-label="Colleagues meeting around a desk in an office" style="left:10.5px;top:16px;width:262px;height:50px"></div>
  <h2 class="abs" style="left:10.5px;top:73px;font-size:9.5px;line-height:10px;font-weight:500"><span class="heading-gold">Heading</span><br>Goes Here</h2>
  <div class="abs" style="left:10.5px;top:96px;width:40px;height:.6px;background:var(--gold)"></div>
  <p class="abs lorem" style="left:10.5px;width:75px;top:104px">Lorem ipsum dolor sit amet, consectetuer adipiscing elit, sed diam nonummy nibh euismod tincidunt ut laoreet dolore magna aliquam erat volutpat. Ut wisi enim ad minim veniam, quis nostrud exerci tation</p>
  <div class="icon" style="left:120px;top:60px"><svg viewBox="0 0 12 12"><circle cx="6" cy="4.5" r="1.7" fill="#fff"/><path d="M3 9.3c.4-2 1.6-2.8 3-2.8s2.6.8 3 2.8z" fill="#fff"/></svg></div>
  <div class="icon" style="left:179px;top:60px"><svg viewBox="0 0 12 12"><circle cx="6" cy="4.5" r="1.7" fill="#fff"/><path d="M3 9.3c.4-2 1.6-2.8 3-2.8s2.6.8 3 2.8z" fill="#fff"/></svg></div>
  <div class="icon" style="left:238px;top:60px"><svg viewBox="0 0 12 12"><circle cx="6" cy="4.5" r="1.7" fill="#fff"/><path d="M3 9.3c.4-2 1.6-2.8 3-2.8s2.6.8 3 2.8z" fill="#fff"/></svg></div>
  <div class="abs center" style="left:104px;width:44px;top:77px;color:var(--white)"><p style="font-size:7px">Heading</p><p class="lorem" style="margin-top:4px">Lorem ipsum dolor sit amet, consectetuer adipiscing elit, sed diam nonummy nibh euismod tincidunt ut laoreet dolore magna aliquam erat volutpat. Ut wisi enim ad minim veniam, quis nostrud exerci tation</p></div>
  <div class="abs center" style="left:163px;width:44px;top:77px;color:var(--white)"><p style="font-size:7px">Heading</p><p class="lorem" style="margin-top:4px">Lorem ipsum dolor sit amet, consectetuer adipiscing elit, sed diam nonummy nibh euismod tincidunt ut laoreet dolore magna aliquam erat volutpat. Ut wisi enim ad minim veniam, quis nostrud exerci tation</p></div>
  <div class="abs center" style="left:222px;width:44px;top:77px;color:var(--white)"><p style="font-size:7px">Heading</p><p class="lorem" style="margin-top:4px">Lorem ipsum dolor sit amet, consectetuer adipiscing elit, sed diam nonummy nibh euismod tincidunt ut laoreet dolore magna aliquam erat volutpat. Ut wisi enim ad minim veniam, quis nostrud exerci tation</p></div>
  <div class="footer-line"></div>
  <span class="footer-brand brand brand-sm">NIVEL CREST</span>
  <span class="footer-page">NIVEL CREST <b>| 01</b></span>
</section>

<!-- Chart slide -->
<section class="slide" style="left:405px;top:502px">
  <h2 class="abs heading-gold" style="left:12px;top:11px;font-size:8.5px">Heading Goes Here</h2>
  <p class="abs lorem" style="left:13px;width:140px;top:41px">Lorem ipsum dolor sit amet, consectetuer adipiscing elit, sed diam nonummy nibh euismod tincidunt ut laoreet dolore magna aliquam erat volutpat. Ut wisi enim ad minim veniam, quis nostrud exerci tation</p>
  <svg class="abs" style="left:10px;top:64px" width="156" height="70" viewBox="0 0 156 70" font-family="Montserrat, Arial, sans-serif" font-size="2.8">
    <g stroke="#d0d0d0" stroke-width=".4">
      <line x1="8" y1="3" x2="155" y2="3"/><line x1="8" y1="13" x2="155" y2="13"/><line x1="8" y1="23" x2="155" y2="23"/><line x1="8" y1="33" x2="155" y2="33"/><line x1="8" y1="43" x2="155" y2="43"/><line x1="8" y1="53" x2="155" y2="53"/><line x1="8" y1="63" x2="155" y2="63"/>
    </g>
    <g fill="#333"><text x="2" y="4">6</text><text x="2" y="14">5</text><text x="2" y="24">4</text><text x="2" y="34">3</text><text x="2" y="44">2</text><text x="2" y="54">1</text><text x="2" y="64">0</text></g>
    <g>
      <rect x="12" y="19" width="8" height="44" fill="#c8963a"/><rect x="23" y="39" width="8" height="24" fill="#6a6a6f"/><rect x="33" y="43" width="8" height="20" fill="#8a8a8e"/>
      <rect x="49" y="38" width="8" height="25" fill="#6a6a6f"/><rect x="59" y="18" width="8" height="45" fill="#c8963a"/><rect x="69" y="43" width="8" height="20" fill="#8a8a8e"/>
      <rect x="86" y="28" width="8" height="35" fill="#5a5a5f"/><rect x="96" y="45" width="8" height="18" fill="#8a8a8e"/><rect x="106" y="33" width="8" height="30" fill="#c8963a"/>
      <rect x="122" y="18" width="8" height="45" fill="#111"/><rect x="132" y="35" width="8" height="28" fill="#7a7a7e"/><rect x="142" y="13" width="8" height="50" fill="#c8963a"/>
    </g>
    <g fill="#333" text-anchor="middle"><text x="27" y="68">Category 1</text><text x="63" y="68">Category 2</text><text x="100" y="68">Category 3</text><text x="136" y="68">Category 4</text></g>
  </svg>
  <div class="abs" role="img" aria-label="Business person reviewing charts at a laptop" style="left:178px;top:27px;width:97px;height:120px;background:linear-gradient(135deg,#2c3140 0%,#56607a 40%,#c7ccd6 70%,#eef0f3 100%)"></div>
  <div class="footer-line"></div>
  <span class="footer-brand brand brand-sm">NIVEL CREST</span>
  <span class="footer-page">NIVEL CREST <b>| 01</b></span>
</section>

<!-- Our Service – progress rings -->
<section class="slide" style="left:78px;top:714px">
  <h2 class="abs" style="left:12px;top:9px;font-size:9px;font-weight:500">Our <span class="heading-gold">Service</span></h2>
  <div class="abs" style="left:12px;top:24px;width:72px;height:.6px;background:var(--gold)"></div>
  <div class="abs" style="left:12px;top:38px;width:14px;height:14px;border-radius:50%;border:.6px solid #bbb;background:var(--white)"></div>
  <div class="icon" style="left:13.5px;top:39.5px;width:11px;height:11px;border:none"><svg viewBox="0 0 12 12"><circle cx="6" cy="4.5" r="1.7" fill="#fff"/><path d="M3 9.3c.4-2 1.6-2.8 3-2.8s2.6.8 3 2.8z" fill="#fff"/></svg></div>
  <div class="abs" style="left:33px;top:39px"><p style="font-size:6.4px">Service Title Goes Here</p><p style="font-size:3.4px">Vivomus eu dull ex. curobour dopibus</p></div>
  <p class="abs lorem" style="left:12px;width:265px;top:55px;text-align:justify">Lorem ipsum dolor sit amet, consectetuer adipiscing elit, sed diam nonummy nibh euismod tincidunt ut laoreet dolore magna aliquam erat volutpat. Ut wisi enim ad minim veniam, quis nostrud exerci tation ullamcorper suscipit lobortis nisl ut aliquip ex ea commodo consequat. Duis autem vel eum iriure dolor in hendrerit in vulputate velit esse molestie consequat.</p>
  <svg class="abs" style="left:0;top:84px" width="287" height="40" viewBox="0 0 287 40" font-family="Montserrat, Arial, sans-serif">
    <g fill="none" stroke-width="2">
      <circle cx="58.5" cy="18.5" r="16" stroke="#111"/><circle cx="58.5" cy="18.5" r="16" stroke="#c8963a" stroke-dasharray="75.4 100.5" transform="rotate(0 58.5 18.5)"/>
      <circle cx="115" cy="18.5" r="16" stroke="#111"/><circle cx="115" cy="18.5" r="16" stroke="#c8963a" stroke-dasharray="75.4 100.5"/>
      <circle cx="170.5" cy="18.5" r="16" stroke="#111"/><circle cx="170.5" cy="18.5" r="16" stroke="#c8963a" stroke-dasharray="75.4 100.5"/>
      <circle cx="227" cy="18.5" r="16" stroke="#111"/><circle cx="227" cy="18.5" r="16" stroke="#c8963a" stroke-dasharray="75.4 100.5"/>
    </g>
    <g fill="#c8963a" font-size="8" text-anchor="middle"><text x="58.5" y="21.5">75%</text><text x="115" y="21.5">75%</text><text x="170.5" y="21.5">75%</text><text x="227" y="21.5">75%</text></g>
  </svg>
  <div class="abs center" style="left:33px;width:52px;top:123px"><p class="heading-gold" style="font-size:5.5px">Heading</p><p style="font-size:3.6px">adipiscing elit. Vivamus<br>eu dui ex. Cutabitur</p></div>
  <div class="abs center" style="left:89px;width:52px;top:123px"><p class="heading-gold" style="font-size:5.5px">Heading</p><p style="font-size:3.6px">adipiscing elit. Vivamus<br>eu dui ex. Cutabitur</p></div>
  <div class="abs center" style="left:144.5px;width:52px;top:123px"><p class="heading-gold" style="font-size:5.5px">Heading</p><p style="font-size:3.6px">adipiscing elit. Vivamus<br>eu dui ex. Cutabitur</p></div>
  <div class="abs center" style="left:201px;width:52px;top:123px"><p class="heading-gold" style="font-size:5.5px">Heading</p><p style="font-size:3.6px">adipiscing elit. Vivamus<br>eu dui ex. Cutabitur</p></div>
  <div class="footer-line"></div>
  <span class="footer-brand brand brand-sm">NIVEL CREST</span>
  <span class="footer-page">NIVEL CREST <b>| 01</b></span>
</section>

<!-- Cards slide -->
<section class="slide" style="left:405px;top:714px">
  <h2 class="abs heading-gold" style="left:12px;top:11px;font-size:8.5px">Heading Goes Here</h2>
  <p class="abs lorem" style="left:10px;width:268px;top:38px">Lorem ipsum dolor sit amet, consectetuer adipiscing elit, sed diam nonummy nibh euismod tincidunt ut laoreet dolore magna aliquam erat volutpat. Ut wisi enim ad minim veniam, quis nostrud exerci tation ullamcorper suscipit lobortis nisl ut aliquip ex ea commodo consequat. Duis autem vel eum iriure dolor in hendrerit in vulputate velit esse molestie consequat.</p>
  <div class="abs center" style="left:21.5px;top:61.5px;width:55px;height:85px;background:linear-gradient(180deg,#2b2b30,#4a4a50 60%,#909094);border-bottom:3px solid var(--gold);color:var(--white)">
    <div style="width:10px;height:10px;border-radius:50%;background:var(--gold);margin:6px auto 0"></div>
    <p style="font-size:6.4px;margin-top:6px">Heading</p>
    <p class="lorem" style="padding:2px 5px 0;font-size:3.4px">Lorem ipsum dolor sit amet, consectetuer adipiscing elit, sed diam nonummy nibh euismod tincidunt ut laoreet dolore magna aliquam erat volutpat. Ut wisi enim ad minim veniam, quis nostrud exerci tation</p>
  </div>
  <div class="abs center" style="left:84px;top:61.5px;width:55px;height:85px;background:linear-gradient(180deg,#c8963a,#d9ae5a 60%,#e6c47c);border-bottom:3px solid var(--ink);color:var(--white)">
    <div style="width:10px;height:10px;border-radius:50%;background:var(--ink);margin:6px auto 0"></div>
    <p style="font-size:6.4px;margin-top:6px">Heading</p>
    <p class="lorem" style="padding:2px 5px 0;font-size:3.4px">Lorem ipsum dolor sit amet, consectetuer adipiscing elit, sed diam nonummy nibh euismod tincidunt ut laoreet dolore magna aliquam erat volutpat. Ut wisi enim ad minim veniam, quis nostrud exerci tation</p>
  </div>
  <div class="abs center" style="left:146px;top:61.5px;width:55px;height:85px;background:linear-gradient(180deg,#2b2b30,#4a4a50 60%,#909094);border-bottom:3px solid var(--gold);color:var(--white)">
    <div style="width:10px;height:10px;border-radius:50%;background:var(--gold);margin:6px auto 0"></div>
    <p style="font-size:6.4px;margin-top:6px">Heading</p>
    <p class="lorem" style="padding:2px 5px 0;font-size:3.4px">Lorem ipsum dolor sit amet, consectetuer adipiscing elit, sed diam nonummy nibh euismod tincidunt ut laoreet dolore magna aliquam erat volutpat. Ut wisi enim ad minim veniam, quis nostrud exerci tation</p>
  </div>
  <div class="abs center" style="left:208.5px;top:61.5px;width:55px;height:85px;background:linear-gradient(180deg,#c8963a,#d9ae5a 60%,#e6c47c);border-bottom:3px solid var(--ink);color:var(--white)">
    <div style="width:10px;height:10px;border-radius:50%;background:var(--ink);margin:6px auto 0"></div>
    <p style="font-size:6.4px;margin-top:6px">Heading</p>
    <p class="lorem" style="padding:2px 5px 0;font-size:3.4px">Lorem ipsum dolor sit amet, consectetuer adipiscing elit, sed diam nonummy nibh euismod tincidunt ut laoreet dolore magna aliquam erat volutpat. Ut wisi enim ad minim veniam, quis nostrud exerci tation</p>
  </div>
  <div class="footer-line"></div>
  <span class="footer-brand brand brand-sm">NIVEL CREST</span>
  <span class="footer-page">NIVEL CREST <b>| 01</b></span>
</section>

<!-- Closing slide -->
<section class="slide" style="left:231px;top:927px;width:288px;height:180px">
  <div class="abs" role="img" aria-label="Office towers photographed from below in warm gold light" style="left:0;top:0;width:288px;height:180px;background:linear-gradient(120deg,#b8862f 0%,#d7ad55 35%,#ecca6d 50%,#c99a40 70%,#8f6a2a 100%)"></div>
  <div class="abs" style="left:20px;top:20px;display:flex;align-items:center;gap:4px">
    <span style="width:10px;height:10px;background:var(--white);display:block"></span>
    <span class="brand brand-lg" style="color:var(--white)">NIVEL CREST</span>
  </div>
  <h2 class="abs" style="left:20px;top:56px;font-size:30px;line-height:30px;font-weight:800;color:var(--white)">THANK<br>YOU!</h2>
  <p class="abs" style="left:20px;top:138px;font-size:12px;line-height:13px;font-weight:700;color:var(--white)">PRESENTATION<br>TITLE GOES HERE</p>
</section>

</body>
</html>
```